Website front end design for an education nonprofit

This project involves design and development of the website front end (i.e., Web user interface and user experience design) for TAVO Sphere, a nonprofit initiative for developing an online platform for basic English language instruction, especially targeted toward underprivileged, non-native English speaking populations.

More about us: We are a team of educators, researchers and engineers passionate about this cause and would like to invite talented, creative web developers to join us in this effort to create positive social impact! Please send a personal message to the project owner for the executive summary to get more information about our initiative, big picture vision and the team.

TAVO Sphere website front end (UI/UX) design
Our key goals for this project are to develop an impressive Drupal-based front end for our website as well as to find really talented and creative web/UI/UX designers-cum-developers who are experts in the state-of-the-art web technologies, and are passionate about the cause of global online basic education. At the end of this project, we hope to have long term engagement with the selected developer(s) for our future website design and development needs.

Here are some preliminary guidelines on the TAVO Sphere website front end framework as envisioned by us so far. Please note that we would very much encourage creative ideas and mock-ups from the developers.

1. Current platform: Our website prototype back-end uses Drupal CMS (we plan to continue using Drupal CMS) and at the moment, a toy front-end is based on the Drupal Skeleton platform for its simplicity, clean UI and mobile device friendliness. The web developer / designer can choose any Drupal front end as a starting point or come up with a new Drupal template that meets our requirements below. Prior experience and expertise on Drupal would be great.

2. Audience profile: While the primary audience for the website is expected to be young kids (6-10 years) not very familiar with English, the secondary audience also includes adults interested in basic English language skills. So the overall goal is to have simple, uncluttered / clean, elegant and lightweight (think loading time as well as mobile device friendliness) interface that is extremely intuitive and easy to navigate, is artistic and aesthetically appealing to a wide audience (especially the non-native English speaking populations). The most important point is that our target audience should feel welcome with the clean, crisp look and easy, user-centric navigation, and should in no case feel overwhelmed (say with too much text or clutter on the front page).

3. Front page: Here is a currently envisioned preliminary sketch of the website front page (very much open for refinement and improvements)
a. The top “menu bar” part of the landing page will have our organization name and logo along with (or above) the top menu bar with the following links and sub-links
i. “Learn” link with sub-menu of all our content sections (World learning, Basic sentence learning, Classic short stories, Picture Dictionary)
ii. “About” links with information about us (sub-menu entries: About TAVO Sphere, Team, Supporters, Contributors)
iii. “Contribute” link with sub-menu entries Donate, Volunteer
iv. Menu entries towards the right side: “Login / sign up” followed by
v. “Search” with space to enter the search phrase
b. The middle “main page content” part of the page is where we would have entry points to our main content categories. The portion is envisioned to be graphical, with big blocks (images) as links to our content categories. The current categories (to start with) include 1. Word learning, 2. Basic sentence learning, and 3. Classic stories. We welcome creative ideas to represent these content categories in an appealing and elegant way (for example, these content categories could be portrayed as closed double doors that lead to the pages with the content. We would like to have placeholders for appropriate image links to different content categories – we should be able to put appropriate images or change them as we come up with new ideas that would work best with our target audience). The categories would change and grow as our content evolves, hence the core idea is to build a flexible framework that readily allows for expansion as well as customization.
c. The bottom menu / links bar portion of the landing page will have a list of links that are not included at the top. Examples include (with flexibility needed to add more when needed)
i. “Help”: this leads to a new page with FAQ, How to use
ii. “Contact us” link to a web contact form page
iii. “For Teachers” link to a page with information such as how to use, tips, pilot programs,
iv. “Volunteer” link to page with links such as Donate, Volunteer
v. “Contributors” that would link to a page with information about our Artists, Teachers, Writers, Developers etc.
vi. “Jobs” would link to a jobs page
vii. “Blog” would lead to our blog page
viii. “User stories” link to pages with feedback that we obtain from the users about how the content has helped them,
ix. Web 2.0 placeholders for social media (to be added later)

d. The footer of the website should include text “2013 TAVO Sphere, All rights reserved.”

4. The middle block of the front page is the largest in screen real estate and perhaps the most challenging part that requires much creativity and thought on the UI/UX design aspect – the content pages pointed to by the section links on the middle portion of the front page are also being designed.

5. Color preference is towards soft, elegant (think grays, whites, light blues, other light colors) web safe colors. No harsh (too bright, garish) colors.

6. Fonts preference Nice, clean looking fonts (Arial alright) compatible across browsers.

7. Portability and robustness of the front page layout for different platforms should be carefully considered. Although our first launch target platform is PC (where cross browser compatibility is important), this would very soon be followed by mobile devices such as tablets and smartphones given their prevalence across the globe. This mobile friendly design or easy portability to mobile platforms with little work requirement should be considered as a design requirement.

8. Front page as a framework for the complete website: Note that the top and the bottom portions of the front page are envisioned be used as a common template / frame across all the pages of our website – the middle portion would be used to show our content on the other pages of our website.

9. UX: For the UI/UX design, it is critical to keep in mind key qualities such as ease of use, simplicity, elegance and artistic appeal. Some specific points to keep in mind: (1) the major portion of the target audience would be new to English and (2) young children are expected to be the primary audience but we want the website to appeal to adults interested in learning as well, and (3) we need the website to work even with relatively slow Internet speeds (for underdeveloped / developing regions especially), should always be kept in mind. HTML5 compliance ideas are encouraged.

10. Strictly not desired: Typical corporate feel seen in many webpages, blocky graphics, dull and uninviting overall look with no personality, Flash type effects, harsh colors.

11. Creativity and imagination necessary: We would like to reiterate that the designer/developer has complete freedom to re-imagine the front page considering the above requirements and get back with ideas for an inspiring layout that presents the content outlined above in an intuitive format, carefully considering our target audience.

A note: As a rule, we will always make sure that our developers and artists get proper credit for their work and are recognized and acknowledged by everyone visiting our website.

Expected deliverables:
Website design psd files AND coded webpage / Drupal template: the corresponding source code and all the required libraries, images etc would be required with minimal documentation / pointers on how to make changes and customizations.

Interested developers are encouraged to first send us preliminary prototype Design for the front page to get feedback on whether their approach and style is in line with our needs and preferences. We will suggest the developers to proceed further if the team thinks there is some potential for a match (of course, the final determination would be from the pool of shortlisted submissions) – otherwise, in case the team does not see potential for a match with our needs or if we have already received multiple submissions that are comparatively more closely aligned with our vision for the website, we'd prefer to be respectful of the developers’ time and effort by requesting them not to proceed further.

Please consider this effort as your contribution to an important social cause of global and accessible online education and not a commercial enterprise (our passion for making a positive impact is what is driving the TAVO Sphere nonprofit team to undertake this initiative!). We would like to invite you to join us in this effort!

Project Deadline Extended
Reason: Due to requests from interested designers, we are extending the deadline. Looking forward to receiving many other creative designs!

Please see the project brief.

Real Estate

• Please see the project brief.

```html
<!DOCTYPE html>
<html lang="en">
<head>
<meta charset="utf-8">
<title>TAVO Sphere – Learn English Online</title>
<link href="https://fonts.googleapis.com/css2?family=Ubuntu:wght@300;400;500&family=Open+Sans:wght@400;600;700&display=swap" rel="stylesheet">
<style>
:root{
  --accent:#1fa3d6;
  --accent-dark:#1a7fa8;
  --teal:#3a98b9;
  --teal-dark:#2f88a8;
  --deep:#1c6b8c;
  --ink:#444;
  --muted:#666;
  --white:#fff;
  --band:#f1f2f3;
}
*{margin:0;padding:0;box-sizing:border-box}
html,body{width:958px;height:1200px;overflow:hidden;background:var(--white)}
body{position:relative;font-family:'Open Sans',Arial,sans-serif;color:var(--ink)}
.abs{position:absolute}
/* header */
.brand{left:144px;top:20px;font-family:'Ubuntu',sans-serif;font-weight:500;font-size:25px;color:#555;letter-spacing:-.3px}
.nav a{position:absolute;top:31px;font-size:8px;font-weight:700;color:#444;text-decoration:none}
.search{left:530px;top:25px;width:148px;height:19px;background:#eeeff0;border:1px solid #e0e0e0;font-size:6.5px;color:#999;padding:5px 8px}
.search svg{position:absolute;right:6px;top:3px}
.btn-top{top:25px;width:60px;height:19px;background:var(--accent);border-bottom:2px solid var(--accent-dark);color:#fff;font-size:7px;text-align:center;line-height:18px}
/* hero */
.hero{left:0;top:67px;width:958px;height:417px;background:linear-gradient(135deg,#3e6b2c 0%,#7aa056 30%,#c9c1a8 55%,#5d7a3a 80%,#2e4a22 100%)}
.hero-arrow{width:50px;height:50px;border-radius:50%;display:flex;align-items:center;justify-content:center}
.cats{left:144px;top:409px;width:670px;height:69px;display:flex}
.cat{position:relative;width:224px;height:69px;background:rgba(0,0,0,.82);border-right:1px solid #333}
.cat h3{position:absolute;left:15px;top:12px;font-family:'Ubuntu',sans-serif;font-weight:400;font-size:13px;color:var(--accent)}
.cat p{position:absolute;left:15px;top:33px;width:150px;font-size:6.8px;line-height:12px;color:#fff}
.cat .go{position:absolute;right:0;top:27px;width:45px;height:42px;background:var(--deep);display:flex;align-items:center;justify-content:center}
/* mission band */
.mission{left:0;top:484px;width:958px;height:84px;background:linear-gradient(#fafafa,var(--band))}
.mission h2{position:absolute;left:144px;top:14px;font-family:'Ubuntu',sans-serif;font-weight:400;font-size:16px;color:var(--accent)}
.mission p{position:absolute;left:144px;top:40px;width:530px;font-size:8px;line-height:15px;color:#444}
.join{left:698px;top:510px;width:117px;height:32px;background:var(--accent);border-bottom:2px solid var(--accent-dark);color:#fff;font-family:'Ubuntu',sans-serif;font-size:9px;text-align:center;line-height:31px}
/* welcome */
.h-sec{font-family:'Ubuntu',sans-serif;font-weight:400;font-size:16px;color:var(--accent)}
.ph{display:block}
.welcome-text{left:346px;top:617px;width:175px;font-size:6.8px;line-height:12.4px;color:#666}
.learn-box{left:678px;top:594px;width:136px;height:122px;background:var(--teal);color:#fff;padding:11px 15px}
.learn-box h3{font-family:'Ubuntu',sans-serif;font-weight:400;font-size:12px}
.learn-box .lead{font-size:6.8px;margin:5px 0 8px}
.learn-box li{list-style:none;font-size:5.6px;line-height:12.2px;text-transform:uppercase}
.learn-box li:before{content:"›";margin-right:4px}
.learn-box .more{position:absolute;right:11px;bottom:9px;border:1px solid #fff;font-size:6px;padding:3px 6px}
/* news */
.pager{top:754px;width:12px;height:12px;background:#7fd0ee;color:#fff;font-size:8px;text-align:center;line-height:11px}
.card{top:777px;width:209px}
.card .img{height:94px;position:relative}
.card .date{position:absolute;left:0;bottom:0;background:var(--teal);color:#fff;font-style:italic;font-size:6.8px;padding:4px 8px}
.card h4{margin-top:10px;font-family:'Ubuntu',sans-serif;font-weight:400;font-size:12px;color:var(--accent)}
.card p{margin-top:6px;font-size:6.4px;line-height:12.4px;color:#666}
.card .more{margin-top:9px;width:62px;height:18px;background:var(--accent);border-bottom:2px solid var(--accent-dark);color:#fff;font-size:5.8px;text-align:center;line-height:17px}
/* footer */
.footer{left:0;top:990px;width:958px;height:181px;background:var(--teal)}
.fcol{position:absolute;color:#fff;text-transform:uppercase}
.fcol h5{font-size:7.5px;font-weight:700;margin-bottom:4px}
.fcol li{list-style:none;font-size:6px;line-height:15.2px}
.fcol h5.gap{margin-top:6px}
.news-note{font-size:5.8px;margin-top:2px}
.email{margin-top:12px;width:161px;height:16px;background:var(--teal-dark);border-bottom:1px solid #6bb9d4;font-size:5.8px;padding:4px 8px}
.send{margin:6px 0 0 110px;width:50px;height:16px;background:#555;font-size:6.4px;text-align:center;line-height:16px}
.social{display:flex;align-items:center;margin-bottom:7px;font-size:6.6px}
.social span.dot{width:20px;height:20px;border-radius:50%;background:var(--deep);margin-right:6px}
.copy{left:0;top:1171px;width:958px;height:29px;background:var(--teal-dark);color:#fff;font-size:5.8px;padding:11px 146px;text-transform:uppercase}
</style>
</head>
<body>

<header>
  <div class="abs brand">TAVO Sphere</div>
  <nav class="nav">
    <a style="left:338px">LEARN</a>
    <a style="left:400px">ABOUT</a>
    <a style="left:462px">CONTRIBUTE</a>
  </nav>
  <div class="abs search">SEARCH :
    <svg width="12" height="12" viewBox="0 0 12 12"><circle cx="5" cy="5" r="3.5" fill="none" stroke="#999" stroke-width="1.3"/><line x1="7.5" y1="7.5" x2="11" y2="11" stroke="#999" stroke-width="1.6"/></svg>
  </div>
  <div class="abs btn-top" style="left:687px">LOGIN</div>
  <div class="abs btn-top" style="left:754px">SIGNUP</div>
</header>

<section class="abs hero" role="img" aria-label="Photo of a group of young students studying together with books and laptops on a lawn"></section>
<div class="abs hero-arrow" style="left:80px;top:250px;background:rgba(180,180,180,.6)">
  <svg width="12" height="20" viewBox="0 0 12 20"><polyline points="10,2 2,10 10,18" fill="none" stroke="#fff" stroke-width="1.5" stroke-dasharray="2 1.5"/></svg>
</div>
<div class="abs hero-arrow" style="left:833px;top:250px;background:rgba(0,0,0,.15)">
  <svg width="12" height="20" viewBox="0 0 12 20"><polyline points="2,2 10,10 2,18" fill="none" stroke="#ccc" stroke-width="1.5" stroke-dasharray="2 1.5"/></svg>
</div>

<div class="abs cats">
  <div class="cat"><h3>WORD LEARNING</h3><p>Lorem Ipsum is simply dummy text of the printing and typesetting industry.</p>
    <div class="go"><svg width="10" height="14" viewBox="0 0 10 14"><polyline points="2,1 8,7 2,13" fill="none" stroke="#fff" stroke-width="2.4"/></svg></div></div>
  <div class="cat"><h3>BASIC SENTENCE LEARNING</h3><p>Lorem Ipsum is simply dummy text of the printing and typesetting industry.</p>
    <div class="go"><svg width="10" height="14" viewBox="0 0 10 14"><polyline points="2,1 8,7 2,13" fill="none" stroke="#fff" stroke-width="2.4"/></svg></div></div>
  <div class="cat" style="border-right:0"><h3>CLASSIC STORIES</h3><p>Lorem Ipsum is simply dummy text of the printing and typesetting industry.</p>
    <div class="go"><svg width="10" height="14" viewBox="0 0 10 14"><polyline points="2,1 8,7 2,13" fill="none" stroke="#fff" stroke-width="2.4"/></svg></div></div>
</div>

<section class="abs mission">
  <h2>We are non profit english learning online platform.</h2>
  <p>Lorem Ipsum is simply dummy text of the printing and typesetting industry. Lorem Ipsum has been the industry's standard dummy text ever since the 1500s</p>
</section>
<div class="abs join">JOIN FOR LEARNING</div>

<h2 class="abs h-sec" style="left:144px;top:585px">Welcome to TAVO Sphere</h2>
<div class="abs ph" style="left:144px;top:614px;width:186px;height:102px;background:linear-gradient(120deg,#c9b7a6,#e9e3de 60%,#f4f4f4)" role="img" aria-label="Photo of a smiling girl using a laptop"></div>
<p class="abs welcome-text">Lorem Ipsum is simply dummy text of the printing and typesetting industry. Lorem Ipsum has been the industry's standard dummy text ever since the 1500s, when an unknown printer took a galley of type and scrambled it to make a type specimen book. It has survived not only five centuries, but also the leap into electronic typesetting, remaining essentially unchanged.</p>
<div class="abs ph" style="left:541px;top:594px;width:137px;height:122px;background:linear-gradient(135deg,#5b6a3a,#2f3a2a 50%,#8a7460)" role="img" aria-label="Photo of a student with a headset at a computer"></div>
<div class="abs learn-box">
  <h3>LEARN</h3>
  <p class="lead">Lorem Ipsum is simply dummy...</p>
  <ul><li>Word Learning</li><li>Basic Sentence Learning</li><li>Classic Short Stories</li><li>Picture Dictionary</li></ul>
  <div class="more">READ MORE</div>
</div>

<h2 class="abs h-sec" style="left:143px;top:741px">Latest news</h2>
<div class="abs pager" style="left:783px">‹</div>
<div class="abs pager" style="left:800px">›</div>

<article class="abs card" style="left:144px">
  <div class="img" style="background:linear-gradient(90deg,#d9dadc,#9aa0a8 40%,#e6e6e6)" role="img" aria-label="Photo of business people standing in an office"><span class="date">Posted on : 27 jun 2013</span></div>
  <h4>Basic sentence learning</h4>
  <p>Lorem Ipsum is simply dummy text of the printing and typesetting industry. Lorem Ipsum has been the industry's standard dummy text ever since the 1500s...</p>
  <div class="more">READ MORE</div>
</article>
<article class="abs card" style="left:376px">
  <div class="img" style="background:linear-gradient(90deg,#ededed,#dcdcdc 50%,#7a7f86)" role="img" aria-label="Photo of a young man with headphones relaxing on a sofa"><span class="date">Posted on : 27 jun 2013</span></div>
  <h4>Basic sentence learning</h4>
  <p>Lorem Ipsum is simply dummy text of the printing and typesetting industry. Lorem Ipsum has been the industry's standard dummy text ever since the 1500s...</p>
  <div class="more">READ MORE</div>
</article>
<article class="abs card" style="left:606px">
  <div class="img" style="background:linear-gradient(135deg,#4f6f34,#9cb878 40%,#c0503c 60%,#3d4f2c)" role="img" aria-label="Photo of students studying on a lawn"><span class="date">Posted on : 27 jun 2013</span></div>
  <h4>Basic sentence learning</h4>
  <p>Lorem Ipsum is simply dummy text of the printing and typesetting industry. Lorem Ipsum has been the industry's standard dummy text ever since the 1500s...</p>
  <div class="more">READ MORE</div>
</article>

<footer class="abs footer">
  <div class="fcol" style="left:144px;top:14px">
    <h5>Welcome</h5>
    <ul><li>Help</li><li>Contact us</li><li>For teachers</li><li>Volunteer</li><li>Contributors</li><li>Jobs</li><li>Blog</li><li>User stories</li></ul>
  </div>
  <div class="fcol" style="left:274px;top:14px">
    <h5>Learn</h5>
    <ul><li>Word learning</li><li>Basic sentence learning</li><li>Classic short stories</li><li>Picture dictionary</li></ul>
    <h5 class="gap">About</h5>
    <ul><li>About TAVO Sphere</li><li>Team</li><li>Supporters</li><li>Contributors</li></ul>
  </div>
  <div class="fcol" style="left:432px;top:21px">
    <h5>Contribute</h5>
    <ul><li>Donate</li><li>Volunteer</li></ul>
    <h5 class="gap" style="margin-top:10px">Newsletter signup</h5>
    <p class="news-note">Get our recent updates through your email :</p>
    <div class="email">Enter your email d :</div>
    <div class="send">SEND</div>
  </div>
  <div class="fcol" style="left:678px;top:18px">
    <div class="social"><span class="dot"></span>: Chatterly</div>
    <div class="social"><span class="dot"></span>: Chirpline</div>
    <div class="social"><span class="dot"></span>: WorkNet</div>
  </div>
</footer>
<div class="abs copy">Copyright 2013 TAVO Sphere. All rights reserved.</div>

</body>
</html>
```